Webdesign für Steuerberaterin
Zielgruppe
Ich bin Steuerberaterin. Meine Zielgruppe sind sowohl Privatpersonen als auch Unternehmer sowie Männer und Frauen.
Aufgabenstellung
Bitte mein Logo und Foto mit berücksichtigen. Ich möchte keine Website, auf der alle 'Reiter' als eine Seite von oben nach unten durchlaufen. Sondern wirklich einzelne, voneinander getrennte Seiten.

```html
<!DOCTYPE html>
<html lang="de">
<head>
<meta charset="utf-8">
<title>Maren Brodtke – Steuerberaterin</title>
<link rel="stylesheet" href="https://fonts.googleapis.com/css2?family=PT+Sans:wght@400;700&family=Tinos&display=swap">
<style>
  :root {
    --sidebar: #1c1a20;
    --gold: #a87d1f;
    --gold-bright: #ddb73b;
    --text: #4a4a4a;
    --white: #ffffff;
    --photo-light: #e4e2e0;
    --photo-dark: #2a2b33;
  }
  * { margin: 0; padding: 0; box-sizing: border-box; }
  html, body { width: 1200px; height: 768px; overflow: hidden; background: var(--white); }
  body { position: relative; font-family: "PT Sans", sans-serif; color: var(--text); }

  .sidebar { position: absolute; left: 0; top: 0; width: 308px; height: 744px; background: var(--sidebar); }

  .portrait {
    position: absolute; left: 61px; top: 35px; width: 317px; height: 230px;
    background: linear-gradient(90deg, var(--photo-light) 0%, #f2f1ef 30%, var(--photo-dark) 48%, var(--photo-dark) 62%, #f0efed 78%, var(--photo-light) 100%);
  }

  .main-nav { position: absolute; left: 64px; top: 290px; list-style: none; }
  .main-nav li { height: 41.5px; }
  .main-nav a { color: var(--gold); text-decoration: none; font-size: 14px; }

  .tag-cloud {
    position: absolute; left: 20px; top: 480px; width: 288px; height: 170px;
    background: radial-gradient(ellipse at 45% 45%, #3a373f 0%, #26232a 55%, var(--sidebar) 100%);
  }

  .legal-nav { position: absolute; left: 68px; top: 704px; font-size: 14px; color: var(--gold); }
  .legal-nav a { color: var(--gold); text-decoration: none; }
  .legal-nav .divider { margin: 0 8px; }

  .brand { position: absolute; left: 400px; top: 172px; display: flex; align-items: center; gap: 8px; }
  .brand-dot { width: 12px; height: 12px; border-radius: 50%; background: var(--gold); }
  .brand-name { font-family: "PT Sans", sans-serif; font-size: 19px; color: var(--gold); }

  .content { position: absolute; left: 606px; top: 0; width: 432px; }
  .welcome-title {
    position: absolute; top: 150px; left: 0; width: 430px; text-align: center;
    font-family: "Tinos", serif; font-weight: 400; font-size: 25px; color: var(--gold);
  }
  .title-rule { position: absolute; top: 202px; left: 0; width: 430px; height: 1.5px; background: var(--gold-bright); }
  .lead { position: absolute; top: 253px; left: 0; font-size: 15.5px; font-weight: 700; white-space: nowrap; }
  .copy { position: absolute; left: 0; font-size: 15px; line-height: 19.3px; white-space: nowrap; }
  .copy-1 { top: 294px; }
  .copy-2 { top: 412px; line-height: 20.5px; }
  .copy-3 { top: 494px; }

  .footer-band { position: absolute; left: 0; top: 746px; width: 1200px; height: 22px; background: var(--gold-bright); }
</style>
</head>
<body>
  <aside class="sidebar">
    <ul class="main-nav">
      <li><a href="#">Über mich</a></li>
      <li><a href="#">Leistungen</a></li>
      <li><a href="#">Kontakt</a></li>
    </ul>
    <div class="tag-cloud" role="img" aria-label="Wortwolke mit Steuerbegriffen wie Steuer, Finanzamt, Mehrwertsteuer und Lohnsteuer"></div>
    <div class="legal-nav"><a href="#">Impressum</a><span class="divider">|</span><a href="#">Datenschutz</a></div>
  </aside>

  <div class="portrait" role="img" aria-label="Porträtfoto der Steuerberaterin vor heller Steinwand"></div>

  <div class="brand">
    <span class="brand-dot"></span>
    <span class="brand-name">Maren Brodtke</span>
  </div>

  <main class="content">
    <h1 class="welcome-title">Schön, dass Sie da sind</h1>
    <div class="title-rule"></div>
    <p class="lead">Ich freue mich, dass Sie den Weg zu mir gefunden haben!</p>
    <p class="copy copy-1">Sie sind bei mir genau richtig:<br>Egal, ob Sie Privatperson sind, die Ihre Einkommensteuer-Erklärung<br>in vertrauensvolle Hände geben möchte,<br>oder Unternehmer, der sich z.B. das „Rundum-Sorglos-Paket“<br>mit Buchführung, Jahresabschluss und Steuererklärungen wünscht.</p>
    <p class="copy copy-2">Schauen Sie sich hier gerne um und melden Sie sich bei mir<br>– ich bin bei jedem steuerlichen Thema gerne Ihr kompetenter<br>und zuverlässiger Ansprechpartner.</p>
    <p class="copy copy-3">Für mich ist es eine Selbstverständlichkeit,<br>dass ich auch nach mehr als 12 Jahren Berufserfahrung<br>durch permanente Fortbildungen immer auf dem aktuellsten Stand<br>der relevanten Gesetze und Verordnungen bin.<br>Nur so kann ich Sie bestmöglich beraten.</p>
  </main>

  <div class="footer-band"></div>
</body>
</html>
```